Professional, Attractive, Simple Website Needed!!

We completed the design for our logo.

We need a website built out around this.

Here are a couple samples of how we want ours formatted.

http://brimvoltco.com

http://www.ravelbeam.com/lp/free-quote?LeadSource=Search%20Engine&ProgramName=searchads&experience=qual&language=en&type=brd&gclid=Xk7PLmqwTRZBNVuEYcaHdFgWsLoPeRtQnMxVbCzJaKiOuYtReWqAsDfGhJkLzXcVbNmQwErTyUiOpAsDfGhJkLzX_wcB

http://quorel.co
Updates

Project Deadline Extended
Reason: Extending this deadline due to our delay in providing designers with content for each page. This is coming in next 24 hours.

Project Deadline Extended
Reason: Due to scheduling conflicts and extended travel delays related to Puerto Rico, the deadline has been extended. Your patience is greatly appreciated.

Project Deadline Extended
Reason: Travel and scheduling conflicts have made it impossible to give this project the thorough review it deserves, therefore I am extending the deadline. Thank you for your patience!

Target Market(s)

Home Owners who earn 60k + household annually

Industry/Entity Type

It Professional

Coding

Coded - Design and coding required

Number of Pages Required

5+ page

Font styles to use
Serif

Colors
34a7d8
9bcb3c

Requirements
Must have
• Simple
• Lead form Entry (Ability for visitor to enter Name, number and address for a quote)
• Sleek Design
• Professional
• Testimonials
• Use color Scheme of Design Logo Attached
Nice to have
• Video when site starts
• Like this
• https://www.vidplexa.com/watch?v=Qm8rTbLw3Np&feature=vidplexa.be
Should not have
• Should not include Commercial solar
• Should not include wind power

```html
<!DOCTYPE html>
<html lang="en">
<head>
<meta charset="utf-8">
<title>Sunmere Energy</title>
<link rel="stylesheet" href="https://fonts.googleapis.com/css2?family=Open+Sans:wght@400;600;700&family=Montserrat:wght@600;700&display=swap">
<style>
:root{
  --blue:#34a7d8;
  --blue-dark:#2a8fbd;
  --green:#9bcb3c;
  --ink:#2c3138;
  --muted:#6d737a;
  --night:#0f1a26;
  --foot:#eef0f2;
  --bar:#dcdfe2;
  --white:#ffffff;
}
*{box-sizing:border-box;margin:0;padding:0}
html,body{width:851px;height:1200px;overflow:hidden}
body{position:relative;background:var(--white);font-family:"Open Sans",Arial,sans-serif;color:var(--ink)}
.hero{position:absolute;left:0;top:0;width:851px;height:350px;background:linear-gradient(180deg,#1c2a3a 0%,#34465a 45%,#5d7186 70%,#3b4a58 100%)}
.hero-shade{position:absolute;inset:0;background:linear-gradient(90deg,rgba(8,14,22,.55),rgba(8,14,22,.2))}
.brand{position:absolute;left:26px;top:16px;display:flex;align-items:center;gap:8px}
.brand-dot{width:26px;height:26px;border-radius:50%;background:var(--blue)}
.brand-name{font-family:"Montserrat",sans-serif;font-weight:700;font-size:12px;color:var(--green);line-height:1.1;width:70px}
.nav{position:absolute;right:12px;top:32px;display:flex;gap:2px}
.nav a{font-family:"Montserrat",sans-serif;font-size:8.5px;font-weight:600;color:var(--white);text-decoration:none;padding:6px 10px;letter-spacing:.3px}
.nav a.active{background:var(--green)}
.hero-title{position:absolute;left:70px;top:172px;font-family:"Montserrat",sans-serif;font-weight:700;font-size:22px;color:var(--white)}
.hero-text{position:absolute;left:70px;top:202px;width:310px;font-size:8.5px;line-height:1.5;color:#dfe6ec}
.lead{position:absolute;left:545px;top:112px;width:238px;height:200px;background:rgba(11,18,28,.88);padding:14px 20px}
.lead h2{font-family:"Montserrat",sans-serif;font-size:17px;color:var(--blue);text-align:center;margin-bottom:14px;letter-spacing:.5px}
.lead .field{display:block;width:100%;height:24px;background:var(--white);border:0;margin-bottom:9px;font-size:8px;padding:0 8px;color:var(--muted);line-height:24px}
.lead .send{display:block;margin:10px auto 0;width:84px;height:24px;background:var(--blue);color:var(--white);font-size:7.5px;font-weight:700;text-align:center;line-height:24px;letter-spacing:.4px}
.services{position:absolute;top:395px;left:0;width:851px}
.card{position:absolute;top:0;width:226px;height:245px;background:var(--white);box-shadow:0 2px 10px rgba(0,0,0,.15);text-align:center;padding-top:24px}
.card svg.icon{width:44px;height:44px}
.card h3{font-family:"Montserrat",sans-serif;font-size:11.5px;font-weight:600;margin:14px 0 10px}
.card p{font-size:7.5px;line-height:1.55;color:var(--muted);padding:0 30px;height:52px}
.card .go{display:flex;align-items:center;justify-content:center;width:26px;height:26px;margin:12px auto 0;border-radius:50%;background:var(--blue)}
.card .go svg{width:12px;height:12px}
.testimonials{position:absolute;top:675px;left:0;width:851px;height:305px;background:linear-gradient(180deg,#3aaee0,#2f9bcc)}
.testimonials h2{text-align:center;margin-top:24px;font-family:"Montserrat",sans-serif;font-size:18px;color:var(--white);letter-spacing:1px}
.quote{position:absolute;top:60px;width:212px}
.quote-box{position:relative;background:var(--white);height:148px;padding:12px 14px}
.quote-box::after{content:"";position:absolute;left:26px;bottom:-8px;border:8px solid transparent;border-bottom:0;border-top-color:var(--white)}
.quote h3{font-family:"Open Sans",sans-serif;font-size:14px;font-weight:600;margin-bottom:8px}
.quote p{font-size:7.5px;line-height:1.6;color:var(--muted)}
.author{display:flex;align-items:center;gap:8px;margin-top:14px;padding-left:14px}
.avatar{width:30px;height:30px;border-radius:50%;background:#d7dce0;border:2px solid var(--white)}
.author b{display:block;font-size:8.5px;color:var(--white)}
.author span{font-size:7px;color:#e3f3fb}
.footer{position:absolute;top:990px;left:0;width:851px;height:180px;background:var(--foot)}
.footer h4{font-size:10px;font-weight:600;margin-bottom:10px}
.col{position:absolute;top:16px}
.links li{list-style:none;font-size:7.5px;color:var(--muted);margin-bottom:5px;padding-left:8px;position:relative}
.links li::before{content:"";position:absolute;left:0;top:4px;width:3px;height:3px;background:var(--green)}
.mail{width:92px;height:18px;background:var(--white);border:1px solid #cfd4d8;font-size:7px;padding:0 5px;line-height:16px;color:var(--muted)}
.subscribe{margin-top:6px;width:52px;height:16px;background:var(--blue);color:var(--white);font-size:7px;text-align:center;line-height:16px}
.contact li{list-style:none;display:flex;gap:8px;font-size:7.5px;color:var(--muted);margin-bottom:9px;line-height:1.4}
.contact svg{flex:none;width:10px;height:10px}
.social{display:flex;gap:5px}
.social i{width:16px;height:16px;border-radius:50%;background:var(--blue);display:block}
.foot-brand{margin-top:14px;display:flex;align-items:center;gap:6px}
.foot-brand .brand-dot{width:22px;height:22px}
.copyright{position:absolute;top:1170px;left:0;width:851px;height:30px;background:var(--bar);text-align:center;font-size:7px;line-height:30px;color:var(--muted)}
</style>
</head>
<body>

<section class="hero" role="img" aria-label="Photo of rooftop solar panels under an evening sky">
  <div class="hero-shade"></div>
</section>

<header class="brand">
  <span class="brand-dot"></span>
  <span class="brand-name">SUNMERE ENERGY</span>
</header>
<nav class="nav">
  <a class="active" href="#">HOME</a><a href="#">ABOUT US</a><a href="#">SERVICES</a><a href="#">TESTIMONIALS</a><a href="#">CONTACT US</a>
</nav>

<h1 class="hero-title">SUNMERE ENERGY</h1>
<p class="hero-text">Solar power made simple for your home. We design, install and maintain clean energy systems that lower your monthly bills and raise the value of your property.</p>

<form class="lead">
  <h2>NEED LEAD</h2>
  <span class="field">Name</span>
  <span class="field">Phone Number</span>
  <span class="field">Address</span>
  <span class="send">GET STARTED</span>
</form>

<section class="services">
  <article class="card" style="left:70px">
    <svg class="icon" viewBox="0 0 44 44" fill="none" stroke="#34a7d8" stroke-width="2"><rect x="7" y="6" width="30" height="24"/><path d="M17 6v24M27 6v24M7 14h30M7 22h30M22 30v8M14 38h16"/></svg>
    <h3>Energy Services</h3>
    <p>We plan and install home solar systems sized to your roof, your usage and your budget, with care from start to finish.</p>
    <span class="go"><svg viewBox="0 0 12 12" fill="none" stroke="#fff" stroke-width="1.8"><path d="M2 6h8M6.5 2.5L10 6l-3.5 3.5"/></svg></span>
  </article>
  <article class="card" style="left:312px">
    <svg class="icon" viewBox="0 0 44 44" fill="none" stroke="#34a7d8" stroke-width="2"><circle cx="22" cy="18" r="3"/><path d="M22 15C20 8 22 4 25 4s3 6-3 11M25 19c7-1 10 2 9 5s-7 1-9-5M19 19c-5 5-9 5-10 2s3-5 10-2M22 21v19M16 40h12"/></svg>
    <h3>Power Saver</h3>
    <p>Smart monitoring and efficient panels help you use less from the grid and keep more money in your pocket every month.</p>
    <span class="go"><svg viewBox="0 0 12 12" fill="none" stroke="#fff" stroke-width="1.8"><path d="M2 6h8M6.5 2.5L10 6l-3.5 3.5"/></svg></span>
  </article>
  <article class="card" style="left:555px">
    <svg class="icon" viewBox="0 0 44 44" fill="none" stroke="#34a7d8" stroke-width="2"><circle cx="22" cy="22" r="6"/><path d="M22 5v6M22 33v6M5 22h6M33 22h6M10 10l4 4M30 30l4 4M34 10l-4 4M14 30l-4 4"/><circle cx="22" cy="22" r="12"/></svg>
    <h3>Solutions</h3>
    <p>Financing, permits and warranties handled by one local team, so going solar is clear, quick and free of hidden surprises.</p>
    <span class="go"><svg viewBox="0 0 12 12" fill="none" stroke="#fff" stroke-width="1.8"><path d="M2 6h8M6.5 2.5L10 6l-3.5 3.5"/></svg></span>
  </article>
</section>

<section class="testimonials">
  <h2>TESTIMONIALS</h2>
  <article class="quote" style="left:85px">
    <div class="quote-box"><h3>Supper Support</h3><p>The crew answered every question and finished the install in two days. Our first bill after the switch was less than half of what we paid before.</p></div>
    <div class="author"><span class="avatar" role="img" aria-label="Customer portrait"></span><div><b>Lena Ward</b><span>Manager, co.</span></div></div>
  </article>
  <article class="quote" style="left:320px">
    <div class="quote-box"><h3>Awesome Work</h3><p>From the first visit to the final inspection the process felt easy. The panels look clean on the roof and the app shows our savings each day.</p></div>
    <div class="author"><span class="avatar" role="img" aria-label="Customer portrait"></span><div><b>Tomas</b><span>Manager, co.</span></div></div>
  </article>
  <article class="quote" style="left:555px">
    <div class="quote-box"><h3>Easy &amp; Fun</h3><p>Signing up took minutes and the team kept us updated at every step. We would gladly recommend them to friends and neighbours looking to go solar.</p></div>
    <div class="author"><span class="avatar" role="img" aria-label="Customer portrait"></span><div><b>Arvid</b><span>Manager, co.</span></div></div>
  </article>
</section>

<footer class="footer">
  <div class="col" style="left:70px">
    <h4>Quick Links</h4>
    <ul class="links"><li>Home</li><li>About Us</li><li>Services</li><li>Testimonials</li><li>Contact Us</li></ul>
  </div>
  <div class="col" style="left:225px">
    <h4>Newsletter</h4>
    <div class="mail">Enter email id</div>
    <div class="subscribe">Subscribe</div>
  </div>
  <div class="col" style="left:460px">
    <h4>Contact Us</h4>
    <ul class="contact">
      <li><svg viewBox="0 0 10 10"><path d="M5 0a3.5 3.5 0 0 0-3.5 3.5C1.5 6 5 10 5 10s3.5-4 3.5-6.5A3.5 3.5 0 0 0 5 0z" fill="#555"/><circle cx="5" cy="3.5" r="1.2" fill="#eef0f2"/></svg><span>1300 Alder Street,<br>Brookvale</span></li>
      <li><svg viewBox="0 0 10 10"><path d="M2 0l2 2.5-1 1.2a6 6 0 0 0 3.3 3.3l1.2-1L10 8l-1.5 2C4 10 0 6 0 1.5z" fill="#555"/></svg><span>(555) 010-4461</span></li>
      <li><svg viewBox="0 0 10 10"><rect y="2" width="10" height="6" fill="#555"/><path d="M0 2l5 3.5L10 2" stroke="#eef0f2" fill="none"/></svg><span>info@sitename.com</span></li>
    </ul>
  </div>
  <div class="col" style="left:690px">
    <h4>Follow Us</h4>
    <div class="social"><i></i><i></i><i></i><i></i></div>
    <div class="foot-brand"><span class="brand-dot"></span><span class="brand-name">SUNMERE ENERGY</span></div>
  </div>
</footer>

<div class="copyright">Copyright © 2017, www.companyname.com. All Rights Reserved.</div>

</body>
</html>
```